Federal IT Consulting Company - Brisolux Consulting Group

We're seeking a skilled web designer to create a modern, bold, and engaging WordPress website for Brisolux Consulting Group, LLC. Our company specializes in federal IT consulting, and our name is a play on "Brightening Solutions." The website should reflect our expertise in the federal technology marketplace and position us as a trusted partner for clients navigating their IT journey.

contact: info@brisoluxgrp-example.com

Current Status

WordPress is already installed on our hosting account
We have an existing logo (may need modernization)

Design Requirements

Style:

Modern and visually striking design
Bold elements to convey confidence and expertise
Incorporate the concept of "brightening solutions" into the design

Features:

Modern UX sliders for dynamic content presentation
Eye-catching, high-quality images (stock photos to be sourced by the designer)
Responsive design for all devices

Color Scheme:

To be proposed by the designer, should align with our brand and convey trust and technological expertise

Logo:

Evaluate our current logo
Create a transparent background version if needed
Propose modernization if deemed necessary

Accessibility:

Ensure design elements are accessible to users with disabilities
Use high contrast ratios for text and background colors
Provide text alternatives for non-text content

Website Structure
Create the following pages, with the possibility of subpages:

Home
Services
About
Contact

Specific Page Requirements
Home Page

Striking hero section with a clear value proposition
Overview of our services
Client testimonials or trust indicators

Services Page

Detailed list of our IT consulting services
Clear explanation of how we help navigate the federal IT landscape

About Page

Company history and mission
Team highlights (if applicable)
Our approach to federal IT consulting

Contact Page

Contact form
Other contact methods (phone, email)

Technical Requirements

Fully responsive design
SEO best practices implemented
Fast loading times
Integration with necessary plugins (to be discussed)
Training on how to update and maintain the site
Full compliance with Web Content Accessibility Guidelines (WCAG) 2.1 Level AA
Adherence to Section 508 standards for federal website accessibility
Implementation of necessary features for ADA compliance
Updates

Designs look the same

Target Market(s)

US Federal Govt customers looking for IT support.

Industry/Entity Type

IT Consulting

Coding

Coded - Design and coding required

Colors
0054AA
0677BA
7BADD7
CADEEF
E8F1F8
0094D4
00A9DD
6FCCEA
C7EBF8
E9F6FB
00AB8E
00BBA5
67D7C9
C6EFE9
E9F9F6

```html
<!DOCTYPE html>
<html lang="en">
<head>
<meta charset="utf-8">
<title>Brisolux Consulting Group</title>
<link href="https://fonts.googleapis.com/css2?family=Lexend:wght@400;500;600;700&family=Outfit:wght@400;500;600;700&family=Plus+Jakarta+Sans:wght@400;500;600;700&display=swap" rel="stylesheet">
<style>
:root{
  --navy:#2a2877;
  --navy-deep:#17164c;
  --accent:#7a72dc;
  --ink:#111122;
  --muted:#44445a;
  --band:#f1f1fb;
  --white:#ffffff;
  --star:#f5b50a;
}
*{box-sizing:border-box;margin:0;padding:0}
html,body{width:1200px;height:3260px;overflow:hidden;background:var(--white)}
body{position:relative;font-family:"Plus Jakarta Sans",sans-serif;color:var(--ink)}
.abs{position:absolute}
.section{position:absolute;left:0;width:1200px}

/* header */
.site-header{top:0;height:70px;background:var(--white)}
.brand{position:absolute;display:flex;align-items:center;gap:10px;font-family:"Lexend",sans-serif;font-weight:700;color:var(--navy)}
.brand-dot{flex:none;width:38px;height:38px;border-radius:50%;background:var(--navy)}
.site-header .brand{left:139px;top:16px;font-size:19px}
.nav{position:absolute;top:0;height:70px;display:flex;align-items:center;font-family:"Outfit",sans-serif;font-size:14px;font-weight:500}
.nav a{position:absolute;color:var(--ink);text-decoration:none;white-space:nowrap}
.nav a.active{color:var(--accent)}
.btn{position:absolute;display:flex;align-items:center;justify-content:center;background:var(--navy);color:var(--white);font-family:"Outfit",sans-serif;font-weight:500;border-radius:8px;box-shadow:0 6px 14px rgba(42,40,119,.28)}

/* hero */
.hero{top:70px;height:529px;overflow:hidden}
.hero-photo{position:absolute;inset:0;background:linear-gradient(90deg,#f3f4f6 0%,#e9edf2 35%,#b8cbe0 55%,#8aa7c8 70%,#6d8a5e 100%)}
.hero-title{left:143px;top:100px;font-family:"Lexend",sans-serif;font-weight:700;font-size:45px;line-height:48px;color:#0c0c16;letter-spacing:.3px}
.hero-sub{left:143px;top:304px;font-family:"Lexend",sans-serif;font-weight:600;font-size:16px;line-height:23px;letter-spacing:3px;color:#111}
.hero .btn{left:141px;top:367px;width:180px;height:44px;border-radius:22px;font-size:13px}

/* about */
.about{top:599px;height:560px}
.photo{position:absolute}
.photo-a{left:134px;top:86px;width:205px;height:381px;border-radius:60px 0 90px 0;background:linear-gradient(160deg,#d9dbe2,#9ea3b3 60%,#6f7487)}
.photo-b{left:352px;top:190px;width:248px;height:339px;border-radius:70px 0 80px 0;background:linear-gradient(160deg,#3c4a57,#6b7b86 55%,#b9b3a8)}
.years-num{left:357px;top:86px;width:71px;height:71px;background:var(--navy);color:var(--white);font-family:"Lexend",sans-serif;font-weight:600;font-size:25px;display:flex;align-items:center;justify-content:center}
.years-label{left:438px;top:86px;width:162px;height:71px;border:1px solid #d6d6e2;border-radius:0 40px 40px 0;padding:14px 18px;font-family:"Lexend",sans-serif;font-size:17px;line-height:21px}
.eyebrow{font-family:"Lexend",sans-serif;color:var(--navy);font-size:21px}
.about .eyebrow{left:658px;top:116px}
.about-title{left:658px;top:141px;font-family:"Lexend",sans-serif;font-weight:700;font-size:33px;line-height:40px;color:#222;letter-spacing:.5px;white-space:nowrap}
.rule{left:658px;top:185px;width:71px;height:3px;background:var(--navy)}
.about-copy{left:658px;width:394px;font-family:"Outfit",sans-serif;font-size:13px;line-height:21.6px;letter-spacing:.3px;color:#1a1a24}
.about-copy.lead{top:205px;font-weight:500}
.about-copy.body{top:276px;color:#33333f}
.about .btn{left:658px;top:458px;width:130px;height:43px;border-radius:10px;font-family:"Lexend",sans-serif;font-size:13px;font-weight:600}

/* services */
.services{top:1159px;height:600px}
.kicker{font-family:"Outfit",sans-serif;font-weight:500;font-size:12.5px;letter-spacing:.6px;color:var(--navy);padding-left:9px;border-left:2px solid var(--navy);line-height:16px}
.services .kicker{left:142px;top:56px}
.section-title{font-family:"Outfit",sans-serif;font-weight:600;font-size:28px;line-height:36px;color:#111}
.section-title em{font-style:normal;color:var(--accent)}
.services .section-title{left:142px;top:84px}
.services .btn{left:957px;top:111px;width:101px;height:43px;font-size:13.5px}
.service-card{position:absolute;top:203px;width:291px;height:262px;border-radius:14px;overflow:hidden}
.service-card .photo{inset:0}
.glass{position:absolute;left:21px;bottom:21px;width:249px;background:rgba(255,255,255,.16);border:1px solid rgba(255,255,255,.75);border-radius:10px;color:var(--white);font-family:"Outfit",sans-serif}
.glass h3{font-weight:500;font-size:15.5px}
.glass p{font-size:12px;line-height:19px;margin-top:10px;width:170px}
.go{position:absolute;right:17px;bottom:20px;width:26px;height:26px;border-radius:50%;background:var(--white);display:flex;align-items:center;justify-content:center}
.slider-arrow{position:absolute;width:38px;height:38px;border-radius:50%;display:flex;align-items:center;justify-content:center}
.slider-arrow.ghost{border:1.5px solid var(--accent);background:var(--white)}
.slider-arrow.solid{background:var(--accent)}

/* trusted */
.trusted{top:1780px;height:580px;background:var(--band);overflow:hidden}
.trusted-mark{left:1060px;top:20px;width:140px;height:140px;border-radius:50%;border:18px solid rgba(122,114,220,.12)}
.trusted-title{left:0;width:1200px;top:60px;text-align:center;font-family:"Lexend",sans-serif;font-weight:600;font-size:33px;color:#1a1a2a}
.trusted-title em{font-style:normal;color:var(--accent)}
.trusted-intro{left:170px;width:860px;top:114px;text-align:center;font-size:12.6px;line-height:21.5px;color:#3a3a4a}
.review{position:absolute;top:194px;width:312px;height:239px;background:var(--white);border-radius:8px;padding:26px 18px}
.review .avatar{position:absolute;left:18px;top:26px;width:54px;height:54px;border-radius:50%;background:linear-gradient(160deg,#d8c8bb,#8c7466)}
.review h4{position:absolute;left:84px;top:30px;font-family:"Lexend",sans-serif;font-weight:500;font-size:16px}
.review .role{position:absolute;left:84px;top:53px;font-size:11.5px;color:#333}
.review .quote{position:absolute;right:20px;top:6px;font-family:"Outfit",sans-serif;font-weight:700;font-size:58px;color:var(--accent);line-height:1}
.review .stars{position:absolute;left:18px;top:90px;color:var(--star);font-size:14px;letter-spacing:2px}
.review p{position:absolute;left:18px;top:116px;width:276px;font-size:12.6px;line-height:19.7px;color:#4a4a58}

/* team */
.team{top:2360px;height:568px}
.team .kicker{left:562px;top:86px}
.team .section-title{left:0;width:1200px;text-align:center;top:113px}
.member{position:absolute;top:198px;width:184px;text-align:center}
.member .portrait{width:184px;height:184px;border-radius:50%;background:radial-gradient(circle at 50% 30%,#f4f2fb 0%,#dcd8f3 60%,#cbc6ee 100%)}
.member h4{margin-top:26px;font-family:"Outfit",sans-serif;font-weight:600;font-size:15.5px}
.member .role{margin-top:4px;font-size:11.5px;color:var(--accent)}
.member .socials{margin-top:12px;display:flex;gap:9px;justify-content:center}
.soc{width:33px;height:33px;border-radius:50%;background:var(--accent)}

/* footer */
.site-footer{top:2928px;height:332px;background:var(--navy-deep);overflow:hidden;color:var(--white)}
.footer-mark{left:1030px;top:30px;width:150px;height:150px;border-radius:50%;border:20px solid rgba(255,255,255,.05)}
.site-footer .brand{left:142px;top:62px;width:300px;font-size:24px;line-height:30px;gap:14px;color:var(--white)}
.site-footer .brand-dot{width:52px;height:52px;background:var(--white)}
.footer-col{position:absolute;top:74px;font-family:"Outfit",sans-serif}
.footer-col h5{font-weight:500;font-size:15px;color:var(--accent);margin-bottom:16px}
.footer-col li{list-style:none;font-size:12.5px;line-height:28px}
.contact-row{display:flex;gap:12px;font-size:12.5px;line-height:17px;margin-bottom:16px}
.contact-row svg{flex:none;margin-top:1px}
.footer-rule{left:142px;top:267px;width:916px;height:1px;background:rgba(255,255,255,.2)}
.copyright{left:142px;top:292px;font-size:12.5px;font-family:"Outfit",sans-serif}
.footer-social{position:absolute;top:287px;left:909px;display:flex;gap:12px}
.footer-social .soc{width:29px;height:29px}
</style>
</head>
<body>

<header class="section site-header">
  <div class="brand"><span class="brand-dot"></span>Brisolux Consulting Group</div>
  <nav class="nav">
    <a class="active" style="left:696px">Home</a>
    <a style="left:770px">About Us</a>
    <a style="left:862px">Services</a>
  </nav>
  <div class="btn" style="left:951px;top:15px;width:107px;height:42px;font-size:14px">Contact Us</div>
</header>

<section class="section hero">
  <div class="hero-photo" role="img" aria-label="Photo of a domed federal capitol building under a bright cloudy sky with trees"></div>
  <h1 class="abs hero-title">NAVIGATE YOUR<br>FEDERAL IT<br>JOURNEY WITH<br>CONFIDENCE</h1>
  <p class="abs hero-sub">EXPERT CONSULTING SERVICES TO<br>GUIDE YOUR IT STRATEGY</p>
  <div class="btn">Explore Our Services</div>
</section>

<section class="section about">
  <div class="photo photo-a" role="img" aria-label="Photo of a consultant presenting a data dashboard to colleagues"></div>
  <div class="abs years-num">15+</div>
  <div class="abs years-label">Year of<br>Experience</div>
  <div class="photo photo-b" role="img" aria-label="Photo of a team working together on laptops in an office"></div>
  <p class="abs eyebrow">ABOUT</p>
  <h2 class="about-title abs">CLEARPATH FORCES</h2>
  <div class="abs rule"></div>
  <p class="abs about-copy lead">Lorem Ipsum is simply dummy text of the printing and typesetting industry. Lorem Ipsum has been the industry's standard dummy text ever since</p>
  <p class="abs about-copy body">Lorem Ipsum is simply dummy text of the printing and typesetting industry. Lorem Ipsum has been the industry's standard dummy text ever since the 1500s, when an unknown printer took a galley of type and scrambled it to make a type specimen book. It has survived not only five centuries, but also the leap into electronic typesetting, remaining essentially unchanged. It was popularised in the 1960s with the release of Letraset sheets containing</p>
  <div class="btn">READ MORE</div>
</section>

<section class="section services">
  <p class="abs kicker">POPULAR SERVICES</p>
  <h2 class="abs section-title">The Best Solution For<br>Your <em>Business</em></h2>
  <div class="btn">View All</div>

  <article class="service-card" style="left:141px">
    <div class="photo" role="img" aria-label="Photo of a dark security operations desk with glowing monitors" style="background:linear-gradient(160deg,#2a1e3c,#3b4a5a 50%,#121820)"></div>
    <div class="glass" style="height:124px;padding:18px 17px">
      <h3>Cybersecurity</h3>
      <p>There are many variations of passages of Lorem Ipsum available.</p>
      <span class="go"><svg width="12" height="12" viewBox="0 0 12 12"><path d="M3 9L9 3M4 3h5v5" stroke="#2a2877" stroke-width="1.4" fill="none"/></svg></span>
    </div>
  </article>
  <article class="service-card" style="left:453px">
    <div class="photo" role="img" aria-label="Photo of a hand touching a glowing cloud network graphic" style="background:linear-gradient(160deg,#3e6c80,#6f99ac 50%,#20343f)"></div>
    <div class="glass" style="height:66px;padding:22px 17px">
      <h3>Cloud Services</h3>
      <span class="go"><svg width="12" height="12" viewBox="0 0 12 12"><path d="M3 9L9 3M4 3h5v5" stroke="#2a2877" stroke-width="1.4" fill="none"/></svg></span>
    </div>
  </article>
  <article class="service-card" style="left:766px">
    <div class="photo" role="img" aria-label="Photo of a strategy meeting around a boardroom table" style="background:linear-gradient(160deg,#8a9a6a,#b48c58 45%,#5a4a3c)"></div>
    <div class="glass" style="height:66px;padding:22px 17px">
      <h3>IT Strategy Consulting</h3>
      <span class="go"><svg width="12" height="12" viewBox="0 0 12 12"><path d="M3 9L9 3M4 3h5v5" stroke="#2a2877" stroke-width="1.4" fill="none"/></svg></span>
    </div>
  </article>

  <div class="slider-arrow ghost" style="left:549px;top:497px"><svg width="18" height="12" viewBox="0 0 18 12"><path d="M17 6H2M6 1L1 6l5 5" stroke="#2a2877" stroke-width="1.6" fill="none"/></svg></div>
  <div class="slider-arrow solid" style="left:613px;top:497px"><svg width="18" height="12" viewBox="0 0 18 12"><path d="M1 6h15M12 1l5 5-5 5" stroke="#fff" stroke-width="1.6" fill="none"/></svg></div>
</section>

<section class="section trusted">
  <div class="abs trusted-mark"></div>
  <h2 class="abs trusted-title"><em>TRUSTED CLIENT</em> AND PARTNERS</h2>
  <p class="abs trusted-intro">Duis aute irure dolor in reprehenderit in voluptate velit esse cillum dolore eu fugiat nulla pariatur. Excepteur sint occaecat cupidatat non proident, sunt in culpa qui officia deserunt mollit anim id est laborum.</p>

  <article class="review" style="left:-223px">
    <span class="quote">&rdquo;</span>
    <p>Lorem ipsum dolor sit amet, consectetur sit adipiscing elit, sed do eiusmod tempor ut incididunt ut labore et dolore magna amet aliqua. Ut enim ad minim veniam, quis dolor nostrud exercitation ullamco.</p>
  </article>
  <article class="review" style="left:111px">
    <div class="avatar" role="img" aria-label="Client portrait"></div>
    <h4>Owen Ratliff</h4><span class="role">Lorem Ipsum</span>
    <span class="quote">&rdquo;</span><span class="stars">★★★★★</span>
    <p>Lorem ipsum dolor sit amet, consectetur sit adipiscing elit, sed do eiusmod tempor ut incididunt ut labore et dolore magna amet aliqua. Ut enim ad minim veniam, quis dolor nostrud exercitation ullamco.</p>
  </article>
  <article class="review" style="left:444px">
    <div class="avatar" role="img" aria-label="Client portrait"></div>
    <h4>Marisol Kent</h4><span class="role">Lorem Ipsum</span>
    <span class="quote">&rdquo;</span><span class="stars">★★★★★</span>
    <p>Lorem ipsum dolor sit amet, consectetur sit adipiscing elit, sed do eiusmod tempor ut incididunt ut labore et dolore magna amet aliqua. Ut enim ad minim veniam, quis dolor nostrud exercitation ullamco.</p>
  </article>
  <article class="review" style="left:777px">
    <div class="avatar" role="img" aria-label="Client portrait"></div>
    <h4>Hana Whitlow</h4><span class="role">Lorem Ipsum</span>
    <span class="quote">&rdquo;</span><span class="stars">★★★★★</span>
    <p>Lorem ipsum dolor sit amet, consectetur sit adipiscing elit, sed do eiusmod tempor ut incididunt ut labore et dolore magna amet aliqua. Ut enim ad minim veniam, quis dolor nostrud exercitation ullamco.</p>
  </article>
  <article class="review" style="left:1111px">
    <div class="avatar" role="img" aria-label="Client portrait"></div>
    <span class="stars">★★★★★</span>
    <p>Lorem ipsum dolor sit amet, consectetur sit adipiscing elit, sed do eiusmod tempor ut incididunt ut labore et dolore magna amet aliqua. Ut enim ad minim veniam, quis dolor nostrud exercitation ullamco.</p>
  </article>

  <div class="slider-arrow ghost" style="left:557px;top:459px;width:35px;height:35px;border-color:#cfcfe0"><svg width="14" height="10" viewBox="0 0 14 10"><path d="M13 5H2M5 1L1 5l4 4" stroke="#111" stroke-width="2" fill="none"/></svg></div>
  <div class="slider-arrow solid" style="left:607px;top:459px;width:35px;height:35px"><svg width="14" height="10" viewBox="0 0 14 10"><path d="M1 5h11M9 1l4 4-4 4" stroke="#fff" stroke-width="2" fill="none"/></svg></div>
</section>

<section class="section team">
  <p class="abs kicker">OUR TEAM</p>
  <h2 class="abs section-title">Meet The Our <em>Experts</em></h2>
  <div class="member" style="left:174px"><div class="portrait" role="img" aria-label="Team member portrait"></div><h4>Elise Marrow</h4><p class="role">Web Designer</p><div class="socials"><span class="soc"></span><span class="soc"></span></div></div>
  <div class="member" style="left:397px"><div class="portrait" role="img" aria-label="Team member portrait"></div><h4>Theo Vance</h4><p class="role">Web Designer</p><div class="socials"><span class="soc"></span><span class="soc"></span></div></div>
  <div class="member" style="left:618px"><div class="portrait" role="img" aria-label="Team member portrait"></div><h4>Priya Dalton</h4><p class="role">Web Designer</p><div class="socials"><span class="soc"></span><span class="soc"></span></div></div>
  <div class="member" style="left:841px"><div class="portrait" role="img" aria-label="Team member portrait"></div><h4>Marcus Hale</h4><p class="role">Web Designer</p><div class="socials"><span class="soc"></span><span class="soc"></span></div></div>
</section>

<footer class="section site-footer">
  <div class="abs footer-mark"></div>
  <div class="brand"><span class="brand-dot"></span><span>Brisolux<br>Consulting Group</span></div>
  <div class="footer-col" style="left:511px"><h5>Quick Links</h5><ul><li>Home</li><li>About Us</li><li>Services</li></ul></div>
  <div class="footer-col" style="left:673px"><h5>Resources</h5><ul><li>Privacy Policy</li><li>Terms Of Service</li></ul></div>
  <div class="footer-col" style="left:852px"><h5>Contact Info</h5>
    <div class="contact-row"><svg width="15" height="17" viewBox="0 0 15 17"><path d="M7.5 16s6-5.5 6-9.5a6 6 0 0 0-12 0c0 4 6 9.5 6 9.5z" fill="none" stroke="#7a72dc" stroke-width="1.6"/><circle cx="7.5" cy="6.5" r="2" fill="#7a72dc"/></svg><span>123 Lorem Ipsum Dummy, #567<br>Dummy Road 1234</span></div>
    <div class="contact-row"><svg width="15" height="12" viewBox="0 0 15 12"><rect x="0" y="0" width="15" height="12" rx="2" fill="#7a72dc"/><path d="M1 2l6.5 5L14 2" stroke="#17164c" stroke-width="1.4" fill="none"/></svg><span>info@brisoluxgrp-example.com</span></div>
    <div class="contact-row"><svg width="15" height="15" viewBox="0 0 15 15"><path d="M3 1l3 3-2 2a9 9 0 0 0 5 5l2-2 3 3-2 2C7 14 1 8 1 3z" fill="#7a72dc"/></svg><span>123-456-7890</span></div>
  </div>
  <div class="abs footer-rule"></div>
  <p class="abs copyright">© 2024 Brisolux Consulting Group. All rights reserved.</p>
  <div class="footer-social"><span class="soc"></span><span class="soc"></span><span class="soc"></span><span class="soc"></span></div>
</footer>

</body>
</html>
```